Brovick Engineering Core Values Branding Package

Brovick Engineering has recently refined its company Core Values and is seeking a strong, cohesive branding package to visually bring these values to life. The new graphic assets will communicate our commitment to excellence in a way that resonates with our team, clients, and partners in a blue-collar, industrial environment.

We are looking for multiple visual assets with consistent design elements that can be applied across platforms. The tone should reflect strength, reliability, and professionalism while remaining approachable and aligned with our industry.

Core Values & Descriptions
Accountability
“We take ownership of our work and actions, ensuring reliability and trust in every solution we deliver.”

Teamwork
“We collaborate across departments and disciplines to provide the highest level of service and innovation for our clients.”

Integrity
“We operate with honesty, transparency, and ethical standards in all aspects of our business.”

Growth
“We are committed to continuous improvement—of our people, our processes, and our impact in the industry.”

Deliverables

1. Primary Core Values Graphic
A master visual representing all four values together.
Designed for use on posters, office signage, internal presentations.

2. Individual Value Graphics (x4)
One graphic per core value: Accountability, Teamwork, Integrity, Growth.
Cohesive style with slight visual variation to reflect each value’s unique meaning.

Target Market(s)

Employees of Brovick Engineering

Industry/Entity Type

Blue Collar

Font styles to use
Sans Serif

Colors
0054AA
0677BA
7BADD7
CADEEF
E8F1F8
00AB8E
00BBA5
67D7C9
C6EFE9
E9F9F6
EB3D1F
EC4F4E
F09395
F8D3D4
FCEDEE

Requirements
Must have
• Accountability, Teamwork, Integrity, Growth

```html
<!DOCTYPE html>
<html lang="en">
<head>
<meta charset="utf-8">
<title>Brovick Engineering – Core Values</title>
<link rel="stylesheet" href="https://fonts.googleapis.com/css2?family=Anton&family=Montserrat:wght@500;600;700&display=swap">
<style>
  :root{
    --green:#3bb02e;
    --navy:#0b2d6b;
    --white:#ffffff;
    --ink:#1a1a1a;
    --badge:#111111;
  }
  *{margin:0;padding:0;box-sizing:border-box}
  html,body{width:731px;height:1200px;overflow:hidden;background:var(--green)}
  .poster{position:relative;width:731px;height:1200px;background:var(--green);font-family:"Montserrat",Arial,sans-serif;overflow:hidden}
  .title{position:absolute;left:52px;top:22px;font-family:"Anton",Impact,sans-serif;font-size:96px;line-height:1;color:var(--white);letter-spacing:-1px;transform:scaleY(1.05);transform-origin:left top}
  .brand{position:absolute;left:528px;top:60px;font-family:"Anton",Impact,sans-serif;font-size:44px;line-height:1;color:var(--navy);letter-spacing:1px}
  .rule{position:absolute;left:52px;width:620px;border-top:2px dotted #0e4a12}
  .rule.top{top:152px}
  .rule.bottom{top:1130px;left:60px;width:600px}
  .band{position:absolute;left:0;width:731px;background:var(--white)}
  .value{position:absolute;width:360px}
  .value-head{display:flex;align-items:center;gap:20px;margin-bottom:20px}
  .badge{background:var(--badge);color:var(--white);font-weight:700;font-size:21px;line-height:1;padding:5px 5px 4px;border-radius:4px;letter-spacing:1px}
  .value-name{font-family:"Anton",Impact,sans-serif;font-size:42px;line-height:1;color:var(--navy);letter-spacing:-0.5px}
  .value-text{font-size:17px;line-height:1.22;color:var(--ink);font-weight:500}
  .medallion{position:absolute;width:240px;height:240px}
  .site{position:absolute;left:0;width:731px;top:1156px;text-align:center;color:var(--white);font-weight:700;font-size:19px;letter-spacing:5px}
</style>
</head>
<body>
<main class="poster">
  <h1 class="title">CORE VALUES</h1>
  <div class="brand">BROVICK</div>
  <div class="rule top"></div>

  <div class="band" style="top:162px;height:232px"></div>
  <div class="band" style="top:408px;height:228px"></div>
  <div class="band" style="top:654px;height:224px"></div>
  <div class="band" style="top:898px;height:224px"></div>

  <!-- Accountability -->
  <svg class="medallion" style="left:29px;top:156px" viewBox="0 0 240 240" aria-hidden="true">
    <circle cx="120" cy="120" r="112" fill="none" stroke="#0e4a12" stroke-width="2" stroke-dasharray="1.5 4"/>
    <circle cx="126" cy="118" r="94" fill="var(--green)"/>
    <circle cx="112" cy="118" r="92" fill="var(--white)"/>
    <circle cx="112" cy="124" r="76" fill="var(--white)" style="filter:drop-shadow(6px 6px 6px rgba(0,0,0,.3))"/>
    <g fill="var(--navy)">
      <rect x="102" y="96" width="30" height="38" rx="2"/>
      <circle cx="96" cy="96" r="13" fill="none" stroke="var(--navy)" stroke-width="5"/>
      <rect x="78" y="106" width="6" height="18" rx="2" transform="rotate(40 81 115)"/>
      <circle cx="136" cy="138" r="9"/>
      <path d="M118 166a18 16 0 0 1 36 0z"/>
      <path d="M86 132a34 34 0 0 0 18 26" fill="none" stroke="var(--navy)" stroke-width="3"/>
      <path d="M150 104a34 34 0 0 1 4 26" fill="none" stroke="var(--navy)" stroke-width="3"/>
    </g>
  </svg>
  <section class="value" style="left:310px;top:218px">
    <div class="value-head"><span class="badge">01</span><h2 class="value-name">ACCOUNTABILITY:</h2></div>
    <p class="value-text">We take ownership of our work and actions, ensuring reliability and trust in every solution we deliver.</p>
  </section>

  <!-- Teamwork -->
  <svg class="medallion" style="left:460px;top:402px" viewBox="0 0 240 240" aria-hidden="true">
    <circle cx="120" cy="120" r="112" fill="none" stroke="#0e4a12" stroke-width="2" stroke-dasharray="1.5 4"/>
    <circle cx="108" cy="116" r="92" fill="var(--navy)"/>
    <circle cx="128" cy="122" r="78" fill="var(--white)" style="filter:drop-shadow(6px 6px 6px rgba(0,0,0,.3))"/>
    <g fill="var(--navy)">
      <path d="M100 112l22-20 24 8 18 20-10 12-24-8-16 14z"/>
      <rect x="86" y="118" width="14" height="30" rx="2" transform="rotate(-40 93 133)"/>
      <rect x="158" y="128" width="14" height="30" rx="2" transform="rotate(40 165 143)"/>
      <path d="M112 136l18-10 20 10-14 14z"/>
    </g>
  </svg>
  <section class="value" style="left:84px;top:460px">
    <div class="value-head"><span class="badge">02</span><h2 class="value-name">TEAMWORK:</h2></div>
    <p class="value-text">We collaborate across departments and disciplines to provide the highest level of service and innovation for our clients.</p>
  </section>

  <!-- Integrity -->
  <svg class="medallion" style="left:29px;top:648px" viewBox="0 0 240 240" aria-hidden="true">
    <circle cx="120" cy="120" r="112" fill="none" stroke="#0e4a12" stroke-width="2" stroke-dasharray="1.5 4"/>
    <circle cx="126" cy="118" r="94" fill="var(--green)"/>
    <circle cx="112" cy="118" r="92" fill="var(--white)"/>
    <circle cx="112" cy="124" r="76" fill="var(--white)" style="filter:drop-shadow(6px 6px 6px rgba(0,0,0,.3))"/>
    <g fill="var(--navy)">
      <circle cx="112" cy="122" r="15"/>
      <circle cx="112" cy="122" r="5" fill="var(--white)"/>
      <path d="M112 102v-6M112 148v-6M92 122h-6M138 122h-6M98 108l-4-4M130 140l-4-4M126 108l4-4M94 140l4-4" stroke="var(--navy)" stroke-width="6"/>
      <path d="M84 112a30 30 0 0 1 42-18M140 132a30 30 0 0 1-42 18" fill="none" stroke="var(--navy)" stroke-width="3"/>
      <circle cx="78" cy="100" r="6"/><path d="M68 118a10 9 0 0 1 20 0z"/>
      <circle cx="146" cy="142" r="6"/><path d="M136 160a10 9 0 0 1 20 0z"/>
    </g>
  </svg>
  <section class="value" style="left:310px;top:696px">
    <div class="value-head"><span class="badge">03</span><h2 class="value-name">INTEGRITY:</h2></div>
    <p class="value-text">We operate with honesty, transparency, and ethical standards in all aspects of our business.</p>
  </section>

  <!-- Growth -->
  <svg class="medallion" style="left:460px;top:900px" viewBox="0 0 240 240" aria-hidden="true">
    <circle cx="120" cy="120" r="112" fill="none" stroke="#0e4a12" stroke-width="2" stroke-dasharray="1.5 4"/>
    <circle cx="108" cy="116" r="92" fill="var(--navy)"/>
    <circle cx="128" cy="122" r="78" fill="var(--white)" style="filter:drop-shadow(6px 6px 6px rgba(0,0,0,.3))"/>
    <g fill="var(--navy)">
      <path d="M128 82l16 18h-9v44h-14v-44h-9z"/>
      <path d="M104 108l11 12h-6v24h-10v-24h-6z"/>
      <path d="M152 108l11 12h-6v24h-10v-24h-6z"/>
      <path d="M96 150h64l6 14h-76z"/>
    </g>
  </svg>
  <section class="value" style="left:84px;top:950px">
    <div class="value-head"><span class="badge">04</span><h2 class="value-name">GROWTH:</h2></div>
    <p class="value-text">We are committed to continuous improvement—of our people, our processes, and our impact in the industry.</p>
  </section>

  <div class="rule bottom"></div>
  <p class="site">WWW.BROVICK.COM</p>
</main>
</body>
</html>
```